I will ask the design of the business card

We are looking for business card design of the new company "R DOVE PAYGRID WORKS LLC." Based in Azerbaijan.
In case
We are working on Azerbaijan to set up the first exchange of crypto currencies.

The key currency used in exchanges is called "PLUME".
In case
We are doing project to make crypto currency infrastructure.

We provide state-of-the-art technology to the world.

```html
<!DOCTYPE html>
<html lang="en">
<head>
<meta charset="utf-8">
<title>R Dove Paygrid Works LLC — Business Card</title>
<link rel="stylesheet" href="https://fonts.googleapis.com/css2?family=Cormorant+Garamond:wght@500&family=Lato:wght@400&display=swap">
<style>
  :root {
    --backdrop: #2a2a2c;
    --card: #1e1e20;
    --silver: #e2e2e2;
    --muted: #b8b8b8;
    --rule: #6f6f72;
  }
  * { box-sizing: border-box; margin: 0; padding: 0; }
  html, body { width: 1200px; height: 1108px; overflow: hidden; }
  body {
    background: var(--backdrop);
    display: flex;
    align-items: center;
    justify-content: center;
    gap: 64px;
  }
  .card {
    width: 380px;
    height: 612px;
    background: var(--card);
    border-radius: 22px;
    box-shadow: 0 18px 40px rgba(0,0,0,0.45);
    position: relative;
    color: var(--silver);
    text-align: center;
  }
  .wordmark {
    font-family: "Cormorant Garamond", Georgia, serif;
    font-weight: 500;
    color: var(--silver);
    letter-spacing: 0.04em;
    line-height: 1.05;
    text-transform: uppercase;
  }
  .card--front .wordmark { position: absolute; top: 78px; left: 0; right: 0; font-size: 34px; }
  .card--back .wordmark { position: absolute; top: 200px; left: 0; right: 0; font-size: 40px; }
  .wordmark span { display: block; }
  .person { position: absolute; top: 300px; left: 0; right: 0; }
  .person__name {
    font-family: "Cormorant Garamond", Georgia, serif;
    font-weight: 500;
    font-size: 26px;
    letter-spacing: 0.06em;
    text-transform: uppercase;
  }
  .person__title { font-family: "Lato", Arial, sans-serif; font-size: 15px; color: var(--muted); margin-top: 2px; }
  .icon-row {
    display: flex; align-items: center; justify-content: center; gap: 8px;
    margin: 14px 40px 8px;
  }
  .icon-row .rule { flex: 1; height: 1px; background: var(--rule); }
  .icon-row svg { width: 20px; height: 20px; }
  .contact { font-family: "Lato", Arial, sans-serif; font-size: 16px; line-height: 1.45; color: var(--silver); }
  .divider { height: 1px; background: var(--rule); margin: 10px 40px; }
</style>
</head>
<body>
  <article class="card card--front">
    <h1 class="wordmark"><span>R Dove</span><span>Paygrid Works</span><span>LLC.</span></h1>
    <section class="person">
      <p class="person__name">Elnur Varga</p>
      <p class="person__title">Managing Director</p>
      <div class="icon-row">
        <span class="rule"></span>
        <svg viewBox="0 0 20 20" aria-label="phone"><circle cx="10" cy="10" r="9.5" fill="#bdbdbd"/><path d="M7 5.5l1.6 0 .8 2.3-1.1.8c.6 1.3 1.6 2.3 2.9 2.9l.8-1.1 2.3.8v1.6c0 .5-.5 1-1 1C9 13.8 6.2 11 6 6.5c0-.5.5-1 1-1z" fill="#1e1e20"/></svg>
        <svg viewBox="0 0 20 20" aria-label="email"><circle cx="10" cy="10" r="9.5" fill="#bdbdbd"/><rect x="5" y="6.5" width="10" height="7" fill="#1e1e20"/><path d="M5 6.5l5 4 5-4" stroke="#bdbdbd" stroke-width="1" fill="none"/></svg>
        <svg viewBox="0 0 20 20" aria-label="website"><circle cx="10" cy="10" r="9.5" fill="#bdbdbd"/><circle cx="10" cy="10" r="5" fill="none" stroke="#1e1e20" stroke-width="1.2"/><ellipse cx="10" cy="10" rx="2" ry="5" fill="none" stroke="#1e1e20" stroke-width="1"/><path d="M5 10h10" stroke="#1e1e20" stroke-width="1"/></svg>
        <span class="rule"></span>
      </div>
      <div class="contact">
        <p>410 555 0193</p>
        <p>hello@dovepaygrid.com</p>
        <p>www.dovepaygrid.com</p>
      </div>
      <div class="divider"></div>
      <div class="contact">
        <p>88 Harbor Row,</p>
        <p>Baku, AZ1010</p>
      </div>
    </section>
  </article>
  <article class="card card--back">
    <p class="wordmark"><span>R Dove</span><span>Paygrid Works</span><span>LLC.</span></p>
  </article>
</body>
</html>
```